Agriculture Business Card

I want to use my existing logo and use my tagline of "Don't Guess...Soil Test" on the card. Looking for a double sided card that will really get peoples attention.
Contact Info:
Marlow Field Crop Edge
Calvin Brusk
2917 K Lane
Larkin, NE 68593
402-555-0193
calvin.r.brusk@fieldmailbox.net

```html
<!DOCTYPE html>
<html lang="en">
<head>
<meta charset="utf-8">
<title>Marlow Field Crop Edge – Business Card</title>
<link rel="stylesheet" href="https://fonts.googleapis.com/css2?family=Open+Sans:wdth,wght@75..100,400..800&display=swap">
<style>
  :root {
    --bg: #c3c4c6;
    --card: #ffffff;
    --green-dark: #2eac4a;
    --green-light: #63ba4b;
    --gold: #f8b322;
    --brown: #8e4a2a;
    --name-brown: #9a5a3c;
  }
  * { margin: 0; padding: 0; box-sizing: border-box; }
  html, body { width: 900px; height: 1200px; overflow: hidden; }
  body {
    background: var(--bg);
    font-family: "Open Sans", Arial, sans-serif;
    font-stretch: 75%;
    position: relative;
  }
  .card {
    position: absolute;
    left: 124px;
    width: 656px;
    height: 375px;
    background: var(--card);
    border-radius: 14px;
    overflow: hidden;
  }
  .card-front { top: 190px; }
  .card-back { top: 622px; }

  .brand { position: absolute; text-align: center; }
  .brand-mark {
    display: block;
    margin: 0 auto 14px;
    border-radius: 50%;
    background: var(--gold);
  }
  .brand-name {
    color: var(--name-brown);
    font-weight: 600;
    line-height: 1.1;
  }
  .card-front .brand { left: 0; right: 0; top: 80px; }
  .card-front .brand-mark { width: 110px; height: 110px; }
  .card-front .brand-name { font-size: 27px; }

  .tagline-band {
    position: absolute;
    left: 0; right: 0; top: 321px; height: 31px;
    background: linear-gradient(90deg, var(--green-dark), var(--green-light));
    color: #fff;
    font-weight: 700;
    font-size: 19px;
    letter-spacing: 1.5px;
    text-align: center;
    line-height: 31px;
  }

  .card-back .brand { left: 116px; width: 170px; top: 112px; }
  .card-back .brand-mark { width: 92px; height: 92px; margin-bottom: 12px; }
  .card-back .brand-name { font-size: 23px; }

  .divider { position: absolute; left: 327px; top: 94px; width: 4px; height: 188px; }

  .contact { position: absolute; left: 374px; top: 88px; color: var(--brown); font-weight: 700; }
  .person-name { font-size: 29px; letter-spacing: 0.5px; line-height: 1.1; }
  .person-name .first { color: var(--green-dark); }
  .person-name .last { color: var(--green-light); }
  .person-role { font-size: 15px; margin-top: 2px; letter-spacing: 0.5px; }
  .rule { width: 104px; height: 1.5px; background: var(--gold); margin: 10px 0 8px; }
  .line { font-size: 15px; letter-spacing: 0.8px; line-height: 26px; }
  .line svg { width: 12px; height: 12px; vertical-align: -1px; margin-right: 6px; fill: var(--green-dark); }
</style>
</head>
<body>
  <section class="card card-front">
    <div class="brand">
      <span class="brand-mark"></span>
      <div class="brand-name">Marlow Field Crop<br>Edge</div>
    </div>
    <div class="tagline-band">DON'T GUESS...SOIL TEST</div>
  </section>

  <section class="card card-back">
    <div class="brand">
      <span class="brand-mark"></span>
      <div class="brand-name">Marlow Field Crop<br>Edge</div>
    </div>

    <svg class="divider" viewBox="0 0 4 188" preserveAspectRatio="none" aria-hidden="true">
      <rect x="1.5" y="0" width="1" height="188" fill="#2eac4a"/>
      <rect x="0" y="32" width="4" height="124" fill="#f8b322"/>
    </svg>

    <div class="contact">
      <div class="person-name"><span class="first">CALVIN</span> <span class="last">BRUSK</span></div>
      <div class="person-role">Owner</div>
      <div class="rule"></div>
      <div class="line">2917 K Lane</div>
      <div class="line">Larkin, NE 68593</div>
      <div class="rule"></div>
      <div class="line">
        <svg viewBox="0 0 24 24" aria-hidden="true"><path d="M6.6 10.8a15.1 15.1 0 0 0 6.6 6.6l2.2-2.2a1 1 0 0 1 1-.25 11.4 11.4 0 0 0 3.6.57 1 1 0 0 1 1 1V20a1 1 0 0 1-1 1A17 17 0 0 1 3 4a1 1 0 0 1 1-1h3.5a1 1 0 0 1 1 1c0 1.25.2 2.45.57 3.57a1 1 0 0 1-.25 1z"/></svg>402-555-0193
      </div>
      <div class="line">
        <svg viewBox="0 0 24 24" aria-hidden="true"><path d="M2 5h20v14H2z M2 5l10 8 10-8" fill="#2eac4a" stroke="#fff" stroke-width="1.5"/></svg>calvin.r.brusk@fieldmailbox.net
      </div>
    </div>
  </section>
</body>
</html>
```